Calm Harbor Bodywork business is seeking a Business Card Design

We are a new natural therapy business that needs a Business Card Design with an appointment card on the back.

We offer Myotherapy (muscle therapy) services and have a strong focus and commitment to helping people relieve pain and restore movement to their bodies.

I am attaching my business logo for you information.

Business card must contain my logo and have space for name, title, qualifications, phone number, email, web address

Appointment Card on the back of the card must contain space to write next appointment date, time and name of therapist and cancellation policy.

Cancellation Policy
Minimum of 24hrs notice is required prior to appointment time or full treatment fees with apply.

```html
<!DOCTYPE html>
<html lang="en">
<head>
<meta charset="utf-8">
<title>Calm Harbor Bodywork – Business and Appointment Card</title>
<link href="https://fonts.googleapis.com/css2?family=Lato:wght@400;700;900&display=swap" rel="stylesheet">
<style>
  :root {
    --page-bg: #3a3a3a;
    --card-bg: #ffffff;
    --brand-red: #c61f3c;
    --brand-brown: #5a4037;
    --brand-green: #78b53a;
    --ink: #333333;
    --dots: #8a8a8a;
  }
  * { box-sizing: border-box; margin: 0; padding: 0; }
  html, body {
    width: 1200px; height: 900px; overflow: hidden;
    background: var(--page-bg);
    font-family: "Lato", Arial, sans-serif;
    color: var(--ink);
  }
  .card-set {
    position: absolute; left: 20px; top: 290px;
    display: flex; gap: 40px;
  }
  .card {
    position: relative;
    width: 560px; height: 320px;
    background: var(--card-bg);
    border-radius: 18px;
    overflow: hidden;
  }

  /* ---------- Appointment side ---------- */
  .appointment-card { padding: 28px 34px; }
  .label {
    display: inline-block;
    background: var(--brand-red);
    color: #fff;
    font-weight: 900;
    text-transform: uppercase;
    letter-spacing: 0.4px;
    padding: 3px 10px;
    line-height: 1.25;
  }
  .label--title { font-size: 18px; }
  .label--policy { font-size: 14px; }
  .meridiem {
    display: flex; justify-content: flex-end; gap: 18px;
    font-size: 12px; height: 18px; align-items: center;
  }
  .field-row {
    display: flex; align-items: baseline; gap: 6px;
    font-size: 13px; text-transform: uppercase; height: 20px;
  }
  .field-line { flex: 1; border-bottom: 2px dotted var(--dots); transform: translateY(-3px); }
  .field-row .gap { width: 16px; }
  .days {
    display: flex; justify-content: space-between;
    margin: 14px 10px 14px 40px;
    font-size: 16px; font-weight: 900; height: 20px; align-items: center;
  }
  .tick-option { display: inline-flex; align-items: center; gap: 5px; }
  .checkbox {
    display: inline-block; width: 18px; height: 17px;
    border: 2px solid var(--brand-red); border-radius: 4px;
  }
  .meridiem .checkbox { width: 16px; height: 14px; }
  .lower { display: flex; justify-content: space-between; align-items: flex-start; margin-top: 20px; }
  .policy-text { margin-top: 8px; font-size: 13px; font-weight: 700; line-height: 1.35; width: 250px; }
  .brand { display: flex; align-items: center; gap: 10px; }
  .appointment-card .brand { margin-top: 6px; }
  .brand-square { width: 52px; height: 52px; background: var(--brand-red); flex: none; }
  .brand-name { font-size: 18px; font-weight: 700; color: var(--brand-red); line-height: 1.15; }

  /* ---------- Business side ---------- */
  .colour-band { display: flex; height: 14px; }
  .colour-band span:nth-child(1) { flex: 38; background: var(--brand-red); }
  .colour-band span:nth-child(2) { flex: 37; background: var(--brand-brown); }
  .colour-band span:nth-child(3) { flex: 25; background: var(--brand-green); }
  .business-body {
    display: flex; justify-content: space-between;
    padding: 40px 34px 0;
  }
  .business-card .brand-square { width: 70px; height: 70px; }
  .business-card .brand-name { font-size: 22px; }
  .person { text-align: right; }
  .person-name {
    font-size: 26px; font-weight: 900; color: var(--brand-green);
    text-transform: uppercase; line-height: 1.1;
  }
  .person-title {
    font-size: 13px; font-weight: 900; text-transform: uppercase;
    letter-spacing: 1px; margin-top: 4px;
  }
  .person-quals { font-size: 12px; margin-top: 4px; }
  .contacts {
    position: absolute; left: 34px; right: 34px; bottom: 30px;
    border-top: 2px solid var(--brand-green);
    padding-top: 14px;
    display: grid; grid-template-columns: 1fr 1fr; row-gap: 8px; column-gap: 16px;
    font-size: 13px;
  }
  .contact { display: flex; align-items: center; gap: 8px; }
  .contact-mark {
    width: 20px; height: 20px; border-radius: 50%;
    background: var(--brand-red); color: #fff;
    font-size: 11px; font-weight: 900;
    display: inline-flex; align-items: center; justify-content: center; flex: none;
  }
</style>
</head>
<body>
  <div class="card-set">
    <section class="card appointment-card">
      <h1 class="label label--title">Next Appointment</h1>

      <div class="meridiem">
        <span class="tick-option">AM <span class="checkbox"></span></span>
        <span class="tick-option">PM <span class="checkbox"></span></span>
      </div>

      <div class="field-row">
        <span>Date:</span><span class="field-line"></span>
        <span class="gap"></span>
        <span>Time:</span><span class="field-line"></span>
      </div>

      <div class="days">
        <span class="tick-option">Mon <span class="checkbox"></span></span>
        <span class="tick-option">Tue <span class="checkbox"></span></span>
        <span class="tick-option">Wed <span class="checkbox"></span></span>
        <span class="tick-option">Thu <span class="checkbox"></span></span>
        <span class="tick-option">Fri <span class="checkbox"></span></span>
      </div>

      <div class="field-row">
        <span>Name of Therapist:</span><span class="field-line"></span>
      </div>

      <div class="lower">
        <div class="policy">
          <h2 class="label label--policy">Cancellation Policy</h2>
          <p class="policy-text">Minimum of 24hrs notice is required prior to appointment time or full treatment fees with apply</p>
        </div>
        <div class="brand">
          <span class="brand-square"></span>
          <span class="brand-name">Calm Harbor<br>Bodywork</span>
        </div>
      </div>
    </section>

    <section class="card business-card">
      <div class="colour-band"><span></span><span></span><span></span></div>
      <div class="business-body">
        <div class="brand">
          <span class="brand-square"></span>
          <span class="brand-name">Calm Harbor<br>Bodywork</span>
        </div>
        <div class="person">
          <p class="person-name">Your Name</p>
          <p class="person-title">Designation</p>
          <p class="person-quals">Qualifications</p>
        </div>
      </div>
      <div class="contacts">
        <span class="contact"><span class="contact-mark">P</span>0400 123 456</span>
        <span class="contact"><span class="contact-mark">E</span>hello@calmharborbodywork.com</span>
        <span class="contact"><span class="contact-mark">W</span>www.calmharborbodywork.com</span>
      </div>
    </section>
  </div>
</body>
</html>
```